Business card for my new company (Accounting firm)

I need a business card for my new business Brightwell Advisory and Ledger SA. Our services are accounting, tax, audit and financial management. Our customers are small companies, start-ups and new companies. The final design has to show financial security, trust and growth. Please find our logo attached to the business card. Text for the business card: Brightwell Advisory and Ledger SA Tomas Varenholt Director and Founder Certified Accountant Tel. 022 418 57 34 tv@clairevalconseil.ch www.clairevalconseil.ch Rue des Vergières 27 1201 Geneva
Target Market(s)
Our customers are small companies, start-ups and new companies.
Industry/Entity Type
Finance And Accounting
Contact Information for Business Card
Claireval Conseil et Comptes SA
Tomas Varenholt
Directeur et Fondateur
Expert-comptable diplômé
Tél. 022 418 57 34
tv@clairevalconseil.ch
www.clairevalconseil.ch
Rue des Vergières 27
1201 Genève

```html
<!DOCTYPE html>
<html lang="fr">
<head>
<meta charset="utf-8">
<title>Claireval Conseil et Comptes SA – Carte de visite</title>
<link rel="stylesheet" href="https://fonts.googleapis.com/css2?family=Montserrat:wght@500&family=Roboto:wght@400;700&display=swap">
<style>
  :root {
    --bg: #e6e7e9;
    --blue-light: #2ea3d8;
    --blue-mid: #1f7fbc;
    --blue-deep: #17598a;
    --ink: #333538;
    --ink-soft: #55585c;
    --accent: #1c6aa6;
    --white: #ffffff;
    --paper: #f7f7f7;
  }
  * { box-sizing: border-box; margin: 0; padding: 0; }
  html, body { width: 1200px; height: 726px; overflow: hidden; }
  body {
    background: var(--bg);
    font-family: "Roboto", Arial, sans-serif;
    position: relative;
  }
  .card {
    position: absolute;
    top: 201px;
    width: 500px;
    height: 324px;
    border-radius: 2px;
    overflow: hidden;
    box-shadow: 0 6px 18px rgba(0,0,0,0.12);
  }
  /* Front */
  .card-front {
    left: 70px;
    background: linear-gradient(160deg, var(--blue-light) 0%, var(--blue-mid) 55%, var(--blue-deep) 100%);
    color: var(--white);
    display: flex;
    flex-direction: column;
    align-items: center;
    justify-content: center;
    text-align: center;
  }
  .wordmark {
    font-family: "Montserrat", Arial, sans-serif;
    font-weight: 500;
    line-height: 1;
  }
  .wordmark-name { display: block; font-size: 44px; letter-spacing: 5px; }
  .wordmark-sub { display: block; font-size: 14px; letter-spacing: 4.2px; margin-top: 8px; }
  .card-front .wordmark { color: var(--white); }
  .front-url {
    margin-top: 34px;
    font-size: 14px;
    font-weight: 700;
    letter-spacing: 0.3px;
  }
  /* Back */
  .card-back {
    left: 630px;
    background: var(--paper);
  }
  .back-band {
    position: absolute;
    left: 0; top: 0;
    width: 120px; height: 100%;
    background: linear-gradient(180deg, var(--blue-light) 0%, var(--blue-mid) 55%, var(--blue-deep) 100%);
  }
  .back-content {
    position: absolute;
    right: 30px;
    top: 30px;
    text-align: right;
  }
  .card-back .wordmark { color: var(--ink); }
  .card-back .wordmark-name { font-size: 40px; letter-spacing: 4.5px; }
  .card-back .wordmark-sub { font-size: 13px; letter-spacing: 3.8px; margin-top: 6px; }
  .person { margin-top: 24px; }
  .person-name { font-size: 19px; font-weight: 700; color: var(--accent); }
  .person-title { font-size: 11.5px; color: var(--ink-soft); line-height: 1.35; }
  .contacts { margin-top: 14px; list-style: none; font-size: 12px; color: var(--ink); line-height: 1.6; }
  .contacts li { display: flex; justify-content: flex-end; align-items: center; gap: 8px; }
  .icon { width: 12px; height: 12px; fill: var(--ink); flex: none; }
  .icon-spacer { width: 12px; flex: none; }
</style>
</head>
<body>
  <section class="card card-front">
    <div class="wordmark">
      <span class="wordmark-name">CLAIREVAL</span>
      <span class="wordmark-sub">CONSEIL ET COMPTES</span>
    </div>
    <p class="front-url">www.clairevalconseil.ch</p>
  </section>

  <section class="card card-back">
    <div class="back-band"></div>
    <div class="back-content">
      <div class="wordmark">
        <span class="wordmark-name">CLAIREVAL</span>
        <span class="wordmark-sub">CONSEIL ET COMPTES</span>
      </div>
      <div class="person">
        <p class="person-name">Tomas Varenholt</p>
        <p class="person-title">Directeur et Fondateur</p>
        <p class="person-title">Expert-comptable diplômé</p>
      </div>
      <ul class="contacts">
        <li>022 418 57 34
          <svg class="icon" viewBox="0 0 24 24"><path d="M6.6 10.8a15 15 0 006.6 6.6l2.2-2.2c.3-.3.7-.4 1-.2 1.1.4 2.3.6 3.6.6.6 0 1 .4 1 1V20c0 .6-.4 1-1 1A17 17 0 013 4c0-.6.4-1 1-1h3.5c.6 0 1 .4 1 1 0 1.3.2 2.5.6 3.6.1.3 0 .7-.2 1z"/></svg>
        </li>
        <li>tv@clairevalconseil.ch
          <svg class="icon" viewBox="0 0 24 24"><path d="M2 5h20v14H2z M4 7v.4l8 5.2 8-5.2V7z" fill-rule="evenodd"/></svg>
        </li>
        <li>www.clairevalconseil.ch
          <svg class="icon" viewBox="0 0 24 24"><circle cx="12" cy="12" r="9.5" fill="none" stroke="#333538" stroke-width="2"/><path d="M2.5 12h19M12 2.5c3 3 3 16 0 19M12 2.5c-3 3-3 16 0 19" fill="none" stroke="#333538" stroke-width="1.6"/></svg>
        </li>
        <li>Rue des Vergières 27 1201 Genève<span class="icon-spacer"></span></li>
      </ul>
    </div>
  </section>
</body>
</html>
```